Corvane Paintless Dent Removal

Our company works on vehicles removing dents using a highly skilled trade which the metal is massaged out with special tools without disturbing the original paint, hence paintless dent removal. Besides keeping the paint and metal original its also very environmentally friendly since no paint or toxic fillers are used. Also we we are one of the most experienced companies in the business with 25 years

Target Market(s)

Retail Automobile consumers, Auto Dealerships and Auto Body Shops

Industry/Entity Type

Auto Repair

Contact Information for Business Card

Dale Hollister
PO Box 518 Brookmere, NY 11962
631-555-0148
corvanepdr@mailbox-example.com
website corvanepdr.example
youtube corvane paintless dent removal
25 years of experience removing Dents, Dings and Hail Damage

Font styles to use
Serif
Sans Serif

Colors

Designer to choose colors to be used in the design.

Requirements
Must have
• I do like things that are simple but classy and somewhat bold, also I like my logo so that should be somewhat important

```html
<!DOCTYPE html>
<html lang="en">
<head>
<meta charset="utf-8">
<title>Corvane Paintless Dent Removal — Business Card</title>
<link rel="stylesheet" href="https://fonts.googleapis.com/css2?family=Roboto:wght@400;700;900&family=Roboto+Condensed:wght@700&display=swap">
<style>
  :root {
    --backdrop: #e9e6e1;
    --card-white: #f7f7f6;
    --navy: #13294b;
    --green: #76bc21;
    --ink-grey: #4a4a4a;
    --gold: #c9a13a;
    --white: #ffffff;
  }
  * { margin: 0; padding: 0; box-sizing: border-box; }
  html, body {
    width: 1200px; height: 960px; overflow: hidden;
    background: var(--backdrop);
    font-family: "Roboto", Arial, sans-serif;
  }
  .stage { position: relative; width: 1200px; height: 960px; }

  .card {
    position: absolute; width: 600px; height: 343px;
    box-shadow: 0 2px 6px rgba(0,0,0,0.25);
  }
  .card--front { left: 314px; top: 113px; background: var(--card-white); }
  .card--back { left: 311px; top: 472px; background: var(--navy); }

  .brand-name {
    position: absolute; text-align: center;
    font-family: "Roboto", Arial, sans-serif; font-weight: 900;
    text-transform: uppercase; line-height: 1;
  }
  .brand-name__main { display: block; font-size: 36px; letter-spacing: 0.5px; }
  .brand-name__sub { display: block; font-size: 15px; margin-top: 4px; letter-spacing: 0.3px; text-transform: none; }

  .card--front .brand-name { right: 34px; top: 56px; width: 280px; color: var(--navy); }
  .card--back .brand-name { left: 0; width: 600px; top: 132px; color: var(--white); }
  .card--back .brand-name__main { font-size: 46px; }
  .card--back .brand-name__sub { font-size: 19px; }

  .holder-name {
    position: absolute; left: 50px; top: 170px;
    font-family: "Roboto Condensed", "Arial Narrow", sans-serif; font-weight: 700;
    font-size: 21px; color: var(--navy); text-transform: uppercase;
  }

  .contact-list { position: absolute; right: 46px; top: 202px; list-style: none; }
  .contact-list li {
    display: flex; justify-content: flex-end; align-items: center;
    height: 19.6px; font-size: 14px; color: var(--ink-grey);
  }
  .contact-list li:last-child { margin-top: 2px; }
  .contact-list .icon { width: 13px; height: 13px; margin-left: 15px; fill: var(--navy); flex: none; }

  .experience-seal {
    position: absolute; right: 26px; top: 19px; width: 68px; height: 68px;
    border-radius: 50%; background: radial-gradient(circle, #1b1b1b 55%, var(--gold) 57%);
  }

  .web-address {
    position: absolute; left: 0; width: 600px; top: 280px; text-align: center;
    color: var(--white); font-size: 14px; letter-spacing: 5.2px;
  }
</style>
</head>
<body>
<main class="stage">

  <section class="card card--front" aria-label="Card front">
    <div class="brand-name">
      <span class="brand-name__main">Corvane</span>
      <span class="brand-name__sub">Paintless Dent Removal</span>
    </div>

    <h1 class="holder-name">Dale Hollister</h1>

    <ul class="contact-list">
      <li>631-555-0148
        <svg class="icon" viewBox="0 0 16 16"><path d="M3.5 1l2.5 3-1.5 2c.8 2 2.5 3.7 4.5 4.5l2-1.5 3 2.5-1.5 2.5C7.5 15 1 8.5 1 2.5z"/></svg>
      </li>
      <li>corvanepdr@mailbox-example.com
        <svg class="icon" viewBox="0 0 16 16"><path d="M1 3h14v10H1z M1 3l7 5 7-5" fill="none" stroke="#13294b" stroke-width="1.6"/></svg>
      </li>
      <li>corvanepdr.example
        <svg class="icon" viewBox="0 0 16 16"><circle cx="8" cy="8" r="6.5" fill="none" stroke="#13294b" stroke-width="1.5"/><path d="M1.5 8h13M8 1.5c-3 3.5-3 9.5 0 13M8 1.5c3 3.5 3 9.5 0 13" fill="none" stroke="#13294b" stroke-width="1.2"/></svg>
      </li>
      <li>corvane paintless dent removal
        <svg class="icon" viewBox="0 0 16 16"><rect x="1" y="3" width="14" height="10" rx="2"/></svg>
      </li>
      <li>PO Box 518 Brookmere, NY 11962
        <svg class="icon" viewBox="0 0 16 16"><path d="M8 1a5 5 0 0 1 5 5c0 4-5 9-5 9S3 10 3 6a5 5 0 0 1 5-5zm0 3a2 2 0 1 0 0 4 2 2 0 0 0 0-4z"/></svg>
      </li>
    </ul>
  </section>

  <section class="card card--back" aria-label="Card back">
    <div class="experience-seal" role="img" aria-label="25 years of experience seal"></div>
    <div class="brand-name">
      <span class="brand-name__main">Corvane</span>
      <span class="brand-name__sub">Paintless Dent Removal</span>
    </div>
    <p class="web-address">www.corvanepdr.example</p>
  </section>

</main>
</body>
</html>
```